velorahelp Web Design Project

It is a virtual assistance/concierge company that helps the busy professional by remotely providing administrative, technical and/or creative business support services, specializing in the medical device industry. Company name is velorahelp.
(website will be velorahelp.example)

Allowing things to be done without taking time away from more urgent issues or family/personal time. Partnering with a VA reduces stress, protects cash flow, eliminates administrative hassles, and enables business people to find the success they originally set out to achieve. Saves small businesses and/or individuals on overhead, salary, et. Work is done remotely to offer administrative, clerical, typing and specialist service assistance on a regular, ad-hoc or emergency cover basis.

Though we are capable of addressing the needs of medical professionals and industry representatives due to our experience and knowledge (sales, HCC guidelines, etc.) we do not want to be limited to that market only.

Target Market(s)

Target market would be M/F, 30-50, National, busy, Alpha, entrepreneurs and industry professionals who want/need to do more without sacrifice of life

Requirements
Nice to have
• We do have a logo designed via the PlanMarket website that can/should be included. Logo is uploaded.

```html
<!DOCTYPE html>
<html lang="en">
<head>
<meta charset="utf-8">
<title>velorahelp – Virtual Assistance</title>
<link rel="stylesheet" href="https://fonts.googleapis.com/css2?family=Open+Sans:wght@400;600&family=Gelasio:ital,wght@0,400;1,400;1,700&display=swap">
<style>
  :root {
    --ink: #333333;
    --muted: #666666;
    --faint: #888888;
    --line: #cfcfcf;
    --accent: #1f73bd;
    --brand-red: #c8202a;
    --brand-navy: #1d2f6b;
    --page: #ffffff;
    --footer-bg: #f4f4f4;
    --sans: "Open Sans", Verdana, sans-serif;
    --serif: "Gelasio", Georgia, serif;
  }
  * { box-sizing: border-box; margin: 0; padding: 0; }
  html, body { width: 722px; height: 1200px; overflow: hidden; background: var(--page); }
  body { position: relative; font-family: var(--sans); color: var(--ink); }
  .abs { position: absolute; }

  .brand { left: 73px; top: 30px; display: flex; align-items: center; gap: 8px; }
  .brand-mark { width: 16px; height: 16px; border-radius: 50%; background: var(--brand-red); }
  .brand-name { font-family: var(--sans); font-weight: 600; font-size: 30px; color: var(--brand-navy); letter-spacing: -0.5px; line-height: 1; }

  .call-us { right: 70px; top: 27px; font-size: 12px; color: var(--muted); }
  .search { left: 518px; top: 51px; width: 134px; height: 24px; border: 1px solid var(--line); border-radius: 3px; font-size: 11px; color: var(--muted); padding: 4px 7px; }
  .search svg { position: absolute; right: 7px; top: 5px; }

  .main-nav { left: 72px; top: 92px; width: 581px; height: 48px; border: 1px solid var(--line); border-radius: 5px; box-shadow: 0 1px 2px rgba(0,0,0,.08); font-size: 13px; color: var(--ink); }
  .main-nav span { position: absolute; top: 16px; }
  .main-nav .current { text-decoration: underline; }

  .hero { left: 73px; top: 152px; width: 580px; height: 242px; background: linear-gradient(100deg, #e9e3df 0%, #f2ede9 35%, #e6d2c6 62%, #f6f3f0 100%); box-shadow: 0 2px 5px rgba(0,0,0,.35); border: 1px solid #e0e0e0; }
  .dots { left: 346px; top: 405px; display: flex; gap: 4px; }
  .dots i { width: 8px; height: 8px; border-radius: 50%; background: #8f8f8f; display: block; }
  .dots i.on { background: var(--accent); }

  .feature { top: 450px; width: 182px; }
  .feature h3 { font-family: var(--serif); font-style: italic; font-weight: 700; font-size: 13px; text-align: center; color: #222; height: 32px; }
  .feature .photo { width: 181px; height: 106px; border: 1px solid #c9c9c9; box-shadow: 0 1px 3px rgba(0,0,0,.25); }
  .feature p { margin-top: 17px; font-size: 12px; line-height: 16px; color: var(--ink); padding-left: 1px; }

  .btn-more { width: 51px; height: 25px; border: 1px solid #c4c4c4; border-radius: 4px; box-shadow: 1px 1px 2px rgba(0,0,0,.2); font-size: 11px; color: var(--accent); display: flex; align-items: center; justify-content: center; background: #fff; }

  .section-title { font-family: var(--serif); font-style: italic; font-size: 14px; color: #333; }
  .section-title b { color: var(--accent); font-weight: 700; }

  .welcome-text { left: 76px; top: 765px; width: 375px; font-size: 12px; line-height: 20px; color: var(--ink); }

  .services { left: 466px; top: 763px; list-style: none; font-size: 12px; color: var(--ink); }
  .services li { display: flex; align-items: center; gap: 9px; height: 24.4px; }

  .clients { left: 73px; top: 959px; width: 580px; height: 156px; border: 1px solid #d4d4d4; border-radius: 4px; box-shadow: 0 1px 4px rgba(0,0,0,.25); }
  .clients .rule { position: absolute; left: 11px; right: 14px; top: 30px; border-top: 1px solid #d0d0d0; }
  .client { position: absolute; top: 41px; width: 125px; }
  .client .photo { width: 125px; height: 75px; border: 1px solid #bdbdbd; background: linear-gradient(135deg, #c8cbc6 0%, #d9c0ab 50%, #eae7e2 100%); }
  .client span { display: block; margin-top: 15px; padding-left: 3px; font-family: var(--serif); font-style: italic; font-size: 11px; color: #333; }

  .site-footer { left: 0; top: 1133px; width: 722px; height: 67px; background: var(--footer-bg); border-top: 1px solid #d8d8d8; }
  .footer-brand { left: 77px; top: 7px; font-family: var(--serif); font-style: italic; font-weight: 700; font-size: 13px; color: var(--muted); text-decoration: underline; }
  .footer-contact { left: 77px; top: 21px; font-size: 9px; line-height: 11px; color: var(--faint); }
  .find-us { left: 530px; top: 19px; font-size: 9px; color: var(--muted); display: flex; align-items: center; gap: 6px; }
  .social { width: 13px; height: 13px; border-radius: 2px; display: block; }
  .copyright { left: 515px; top: 38px; font-size: 9px; color: var(--muted); }
</style>
</head>
<body>

<header>
  <div class="abs brand"><span class="brand-mark"></span><span class="brand-name">velorahelp</span></div>
  <div class="abs call-us">Call us @ 1800 - 55 - 730418</div>
  <div class="abs search">search...
    <svg width="13" height="13" viewBox="0 0 13 13"><circle cx="5" cy="5" r="3.8" fill="none" stroke="#888" stroke-width="1.6"/><line x1="8" y1="8" x2="12" y2="12" stroke="#888" stroke-width="2"/></svg>
  </div>
  <nav class="abs main-nav">
    <span class="current" style="left:30px">Home</span>
    <span style="left:110px">|</span>
    <span style="left:158px">About Us</span>
    <span style="left:262px">|</span>
    <span style="left:310px">Our Services</span>
    <span style="left:437px">|</span>
    <span style="left:481px">Contact Us</span>
  </nav>
</header>

<div class="abs hero" role="img" aria-label="Smiling support agent wearing a headset, colleagues blurred behind"></div>
<div class="abs dots"><i class="on"></i><i></i><i></i><i></i></div>

<section class="abs feature" style="left:74px">
  <h3>Recieving calls</h3>
  <div class="photo" role="img" aria-label="Agent with headset taking a call in an office" style="background:linear-gradient(110deg,#b8a36a 0%,#d9cfb6 45%,#6b5544 75%,#e8e4de 100%)"></div>
  <p>Put here something about collection of client query or calls to researching over them in a brief.</p>
  <div class="btn-more" style="margin-top:19px">More</div>
</section>
<section class="abs feature" style="left:273px">
  <h3>Reserching Issues</h3>
  <div class="photo" role="img" aria-label="Man researching at a desk with two monitors" style="background:linear-gradient(110deg,#4f6a4a 0%,#8ea0b8 40%,#c9b8a8 70%,#8a9ab0 100%)"></div>
  <p>Put here something about researching of client query or calls to researching over them in a brief.</p>
  <div class="btn-more" style="margin-top:19px">More</div>
</section>
<section class="abs feature" style="left:471px">
  <h3>Resolving Problems</h3>
  <div class="photo" role="img" aria-label="Two business people shaking hands" style="background:linear-gradient(120deg,#2e3a55 0%,#a9c3dc 40%,#d9b49a 60%,#27324a 100%)"></div>
  <p>Put here something about resolving of client query or calls to researching over them in a brief.</p>
  <div class="btn-more" style="margin-top:19px">More</div>
</section>

<h2 class="abs section-title" style="left:75px;top:737px"><b>Welcome</b> to our site</h2>
<p class="abs welcome-text">It is a virtual assistance/concierge company that helps the busy professional by remotely providing administrative, technical and/or creative business support services, specializing in the medical device industry. Company name is velorahelp. It is a virtual assistance/concierge company that helps the busy professional by remotely providing administrative, technical and/or creative business support services.</p>
<div class="abs btn-more" style="left:75px;top:917px">More</div>

<h2 class="abs section-title" style="left:465px;top:737px"><b>Our</b> Services</h2>
<ul class="abs services">
  <li><svg width="15" height="15" viewBox="0 0 15 15"><circle cx="7.5" cy="7.5" r="6.5" fill="#f3f6f8" stroke="#b9c3cc"/><path d="M6 4.8 L10 7.5 L6 10.2Z" fill="#2a8fc8"/></svg>Service goes here</li>
  <li><svg width="15" height="15" viewBox="0 0 15 15"><circle cx="7.5" cy="7.5" r="6.5" fill="#f3f6f8" stroke="#b9c3cc"/><path d="M6 4.8 L10 7.5 L6 10.2Z" fill="#2a8fc8"/></svg>Service goes here</li>
  <li><svg width="15" height="15" viewBox="0 0 15 15"><circle cx="7.5" cy="7.5" r="6.5" fill="#f3f6f8" stroke="#b9c3cc"/><path d="M6 4.8 L10 7.5 L6 10.2Z" fill="#2a8fc8"/></svg>Service goes here</li>
  <li><svg width="15" height="15" viewBox="0 0 15 15"><circle cx="7.5" cy="7.5" r="6.5" fill="#f3f6f8" stroke="#b9c3cc"/><path d="M6 4.8 L10 7.5 L6 10.2Z" fill="#2a8fc8"/></svg>Service goes here</li>
  <li><svg width="15" height="15" viewBox="0 0 15 15"><circle cx="7.5" cy="7.5" r="6.5" fill="#f3f6f8" stroke="#b9c3cc"/><path d="M6 4.8 L10 7.5 L6 10.2Z" fill="#2a8fc8"/></svg>Service goes here</li>
  <li><svg width="15" height="15" viewBox="0 0 15 15"><circle cx="7.5" cy="7.5" r="6.5" fill="#f3f6f8" stroke="#b9c3cc"/><path d="M6 4.8 L10 7.5 L6 10.2Z" fill="#2a8fc8"/></svg>Service goes here</li>
</ul>
<div class="abs btn-more" style="left:464px;top:917px">More</div>

<section class="abs clients">
  <h2 class="abs section-title" style="left:12px;top:7px"><b>Our</b> Clients</h2>
  <svg class="abs" style="left:529px;top:8px" width="36" height="15" viewBox="0 0 36 15">
    <circle cx="7" cy="7.5" r="6.3" fill="#f3f6f8" stroke="#b9c3cc"/><path d="M9 4.8 L5 7.5 L9 10.2Z" fill="#2a8fc8"/>
    <circle cx="26" cy="7.5" r="6.3" fill="#f3f6f8" stroke="#b9c3cc"/><path d="M24 4.8 L28 7.5 L24 10.2Z" fill="#2a8fc8"/>
  </svg>
  <div class="rule"></div>
  <div class="client" style="left:10px"><div class="photo" role="img" aria-label="Client representative portrait"></div><span>Lindenfield Clinic</span></div>
  <div class="client" style="left:154px"><div class="photo" role="img" aria-label="Client representative portrait"></div><span>Lindenfield Clinic</span></div>
  <div class="client" style="left:298px"><div class="photo" role="img" aria-label="Client representative portrait"></div><span>Lindenfield Clinic</span></div>
  <div class="client" style="left:439px"><div class="photo" role="img" aria-label="Client representative portrait"></div><span>Lindenfield Clinic</span></div>
</section>

<footer class="abs site-footer">
  <div class="abs footer-brand">velorahelp</div>
  <div class="abs footer-contact">Emergency Call : 1800-00-4417<br>Fax : 5550142287<br>E-mail : help4@velorahelp.example</div>
  <div class="abs find-us">Find Us :
    <span class="social" style="background:#3b5a9a" role="img" aria-label="Social profile one"></span>
    <span class="social" style="background:#4fa8d8" role="img" aria-label="Social profile two"></span>
    <span class="social" style="background:#2a6ea6" role="img" aria-label="Social profile three"></span>
  </div>
  <div class="abs copyright">Copyright 2012 | Privacy Policy</div>
</footer>

</body>
</html>
```